Business Card Design

New business card design

Target Market(s)

Residential & Commercial Property Managers

Industry/Entity Type

Plumbing Services

Contact Information for Business Card

Name - Rowan Keddle, title - Director, Phone Number - 0431 286 517, email - rowan@tbk-plumbing.com.au, Company ABN - 73 215 904 386,

Font styles to use
Sans Serif

Colors
0054AA
0677BA
7BADD7
CADEEF
E8F1F8

```html
<!DOCTYPE html>
<html lang="en">
<head>
<meta charset="utf-8">
<title>TBK Plumbing Services – Business Card</title>
<link rel="stylesheet" href="https://fonts.googleapis.com/css2?family=Roboto:wght@400;500;700&display=swap">
<style>
  :root {
    --stage: #ececec;
    --card: #1e222a;
    --edge: #0677ba;
    --accent: #1e9ee0;
    --accent-band: #0f8fd6;
    --ink: #ffffff;
    --ink-soft: #c9ced6;
    --rule: #d9dde3;
  }
  * { box-sizing: border-box; margin: 0; padding: 0; }
  html, body { width: 1200px; height: 900px; overflow: hidden; }
  body {
    background: var(--stage);
    font-family: "Roboto", Arial, sans-serif;
    display: flex;
    align-items: center;
    justify-content: center;
    gap: 60px;
  }
  .card {
    position: relative;
    width: 520px;
    height: 316px;
    border-radius: 22px;
    background: var(--card);
    border: 4px solid var(--edge);
    overflow: hidden;
    box-shadow: 0 18px 40px rgba(0,0,0,0.28);
  }
  .contact {
    position: absolute;
    left: 34px;
    top: 40px;
    width: 260px;
  }
  .contact__name {
    color: var(--accent);
    font-weight: 700;
    font-size: 22px;
    letter-spacing: 0.5px;
    text-transform: uppercase;
  }
  .contact__title {
    color: var(--ink-soft);
    font-size: 14px;
    margin-top: 3px;
  }
  .contact__rule {
    height: 1px;
    background: var(--rule);
    margin: 12px 0;
    width: 150px;
  }
  .contact__line {
    display: flex;
    align-items: center;
    gap: 8px;
    color: var(--ink-soft);
    font-size: 14px;
    margin-bottom: 7px;
    white-space: nowrap;
  }
  .contact__line svg { width: 12px; height: 12px; flex: none; }
  .divider {
    position: absolute;
    inset: 0;
    width: 100%;
    height: 100%;
    pointer-events: none;
  }
  .abn-band {
    position: absolute;
    left: 0;
    bottom: 0;
    width: 100%;
    height: 46px;
  }
  .abn-band__text {
    position: absolute;
    left: 34px;
    bottom: 12px;
    color: var(--ink);
    font-size: 16px;
    letter-spacing: 0.3px;
  }
  .brand {
    position: absolute;
    display: flex;
    align-items: center;
    gap: 10px;
  }
  .brand__mark {
    width: 14px;
    height: 14px;
    border-radius: 50%;
    background: var(--accent);
    flex: none;
  }
  .brand__name {
    color: var(--ink);
    font-weight: 500;
    font-size: 20px;
    letter-spacing: 0.5px;
    white-space: nowrap;
  }
  .card--front .brand { right: 32px; top: 178px; }
  .card--back .brand { left: 56px; top: 70px; }
</style>
</head>
<body>

  <section class="card card--front" aria-label="Business card, contact side">
    <svg class="divider" viewBox="0 0 512 308" aria-hidden="true">
      <line x1="190" y1="168" x2="300" y2="262" stroke="var(--rule)" stroke-width="1"/>
    </svg>

    <div class="contact">
      <p class="contact__name">Rowan Keddle</p>
      <p class="contact__title">Director</p>
      <div class="contact__rule"></div>
      <p class="contact__line">
        <svg viewBox="0 0 12 12" aria-hidden="true"><path d="M3 1 L5 3.4 L3.8 4.8 Q5 7.2 7.2 8.2 L8.6 7 L11 9 L9.6 11 Q4.5 10.6 1 3 Z" fill="var(--ink-soft)"/></svg>
        0431 286 517
      </p>
      <p class="contact__line">
        <svg viewBox="0 0 12 12" aria-hidden="true"><rect x="1" y="2.5" width="10" height="7" rx="1" fill="var(--ink-soft)"/><path d="M1.5 3 L6 6.5 L10.5 3" fill="none" stroke="var(--card)" stroke-width="1"/></svg>
        rowan@tbk-plumbing.com.au
      </p>
    </div>

    <div class="brand">
      <span class="brand__mark"></span>
      <span class="brand__name">TBK Plumbing Services</span>
    </div>

    <svg class="abn-band" viewBox="0 0 512 46" preserveAspectRatio="none" aria-hidden="true">
      <polygon points="0,0 300,0 330,46 0,46" fill="var(--accent-band)"/>
      <polygon points="300,0 308,0 338,46 330,46" fill="var(--ink)"/>
    </svg>
    <p class="abn-band__text">ABN: 73 215 904 386</p>
  </section>

  <section class="card card--back" aria-label="Business card, brand side">
    <div class="brand">
      <span class="brand__mark"></span>
      <span class="brand__name">TBK Plumbing Services</span>
    </div>
  </section>

</body>
</html>
```